BrivoTerna. Lantern of the Steady Harvest. Business card

Professional business card for BrivoTerna (Lantern of the Steady Harvest)
My rationale: Strategy-> Execution-> Results-> Value that lead to the BrivoTerna name: We put the Lantern of the Steady Harvest.
We deliver value to our customers helping them at defining a good strategy (cyan arrow). 90% of well formulated strategies fail due to poor execution so we also consider strategical execution very important (green arrow). Due to the execution we obtain the results (blue arrow). Finally, the results provide feedback to redefine strategy, and the new strategy has to be executed and new results obtained providing new feedback and on and on. It's like a wheel that finally, must create corporate value: value for shareholders, staholders, employees, providers...-

Target Market(s)

CEOs and steering comitees , invewrnent funds

Industry/Entity Type

Business Consultant

Contact Information for Business Card

Teodoro Vinsquel
CEO & Founder
teodoro.vinsquel@brivoterna-example.com
Mobile: +34 655.803.912
www.brivoterna-example.com

Colors

Designer to choose colors to be used in the design.

Requirements
Nice to have
• Nice to hace the words: Strategy, execution, results
• Nice to vave the claim: Lantern of the Steady Harvest
• The three colors should be shown:
• cyan for STRATEGY
• green for EXECUTION
• blue for RESULTS
Should not have
• Complete black background

```html
<!DOCTYPE html>
<html lang="en">
<head>
<meta charset="utf-8">
<title>BrivoTerna – Business Card</title>
<link rel="stylesheet" href="https://fonts.googleapis.com/css2?family=Arimo:wght@400;700&display=swap">
<style>
  :root {
    --backdrop: #e9e9ec;
    --brand-blue: #233f94;
    --brand-green: #8dc63f;
    --text-grey: #3a3a3a;
    --card-white: #ffffff;
  }
  * { box-sizing: border-box; margin: 0; padding: 0; }
  html, body {
    width: 1200px; height: 852px; overflow: hidden;
    background: var(--backdrop);
    font-family: "Arimo", Arial, sans-serif;
  }
  .stage {
    position: relative; width: 1200px; height: 852px;
    display: flex; align-items: center; justify-content: center; gap: 40px;
  }
  .card {
    position: relative; width: 540px; height: 310px;
    border-radius: 22px; overflow: hidden;
    box-shadow: 0 6px 18px rgba(0,0,0,0.18);
  }
  .card--front { background: var(--brand-blue); }
  .card--back { background: var(--card-white); }

  .wordmark {
    position: absolute; font-weight: 700; letter-spacing: -1px; line-height: 1;
  }
  .card--front .wordmark {
    right: 34px; top: 148px; font-size: 54px; color: var(--card-white);
  }
  .card--back .wordmark {
    right: 34px; top: 70px; font-size: 44px; color: var(--brand-blue);
  }

  .contact {
    position: absolute; left: 40px; bottom: 30px;
  }
  .contact__name {
    font-size: 26px; font-weight: 700; color: var(--brand-green); line-height: 1.1;
  }
  .contact__role {
    font-size: 17px; color: var(--text-grey); margin: 4px 0 12px;
  }
  .contact__list { list-style: none; }
  .contact__item {
    display: flex; align-items: center; gap: 9px;
    font-size: 14px; color: var(--text-grey); line-height: 1.55;
  }
  .contact__icon { width: 13px; height: 13px; flex: none; }
</style>
</head>
<body>
<main class="stage">

  <section class="card card--front" aria-label="Business card front">
    <span class="wordmark">BrivoTerna</span>
  </section>

  <section class="card card--back" aria-label="Business card back">
    <span class="wordmark">BrivoTerna</span>

    <div class="contact">
      <p class="contact__name">Teodoro Vinsquel</p>
      <p class="contact__role">CEO &amp; Founder</p>
      <ul class="contact__list">
        <li class="contact__item">
          <svg class="contact__icon" viewBox="0 0 14 14" aria-hidden="true">
            <rect x="3" y="0.8" width="8" height="12.4" rx="1.6" fill="none" stroke="var(--brand-blue)" stroke-width="1.6"/>
            <circle cx="7" cy="10.6" r="0.9" fill="var(--brand-blue)"/>
          </svg>
          +34 655.803.912
        </li>
        <li class="contact__item">
          <svg class="contact__icon" viewBox="0 0 14 14" aria-hidden="true">
            <rect x="0.5" y="2.5" width="13" height="9" fill="var(--brand-blue)"/>
            <path d="M0.8 3 L7 8 L13.2 3" fill="none" stroke="#fff" stroke-width="1.1"/>
          </svg>
          teodoro.vinsquel@brivoterna-example.com
        </li>
        <li class="contact__item">
          <svg class="contact__icon" viewBox="0 0 14 14" aria-hidden="true">
            <circle cx="7" cy="7" r="6" fill="var(--brand-blue)"/>
            <path d="M1.2 7 H12.8 M7 1 C4.3 4 4.3 10 7 13 M7 1 C9.7 4 9.7 10 7 13" fill="none" stroke="#fff" stroke-width="0.9"/>
          </svg>
          www.brivoterna-example.com
        </li>
      </ul>
    </div>
  </section>

</main>
</body>
</html>
```